Tidewell Homecare

I am looking to have a website designed for a housekeeping company that looks similar to this one. https://marloweshomecare.example/

I need 5 websites designed but will start with this one to see how I like it.

Industry/Entity Type

House Cleaning

Coding

Coded - Design and coding required

Number of Pages Required

5+ page

Font styles to use
Serif
Script

Colors
ffffff
fdf9cf
fbf289
fbee3f
d6edf3
86cae7
33a6d7
edf1f8
cedeed

```html
<!DOCTYPE html>
<html lang="en">
<head>
<meta charset="utf-8">
<title>Tidewell Homecare</title>
<link rel="stylesheet" href="https://fonts.googleapis.com/css2?family=Roboto+Slab:wght@300;400;700&family=Roboto:wght@400;500;700&display=swap">
<style>
:root{
  --white:#ffffff;
  --cream:#fdf9cf;
  --lemon:#fbf289;
  --yellow:#fbee3f;
  --ice:#d6edf3;
  --sky:#86cae7;
  --blue:#33a6d7;
  --btn-blue:#2f8fd0;
  --mist:#edf1f8;
  --steel:#cedeed;
  --ink:#222222;
  --text:#444444;
  --muted:#666666;
  --footer:#f4f4f4;
  --line:#d0d0d0;
}
*{box-sizing:border-box;margin:0;padding:0}
html,body{width:1200px;height:3735px;overflow:hidden}
body{font-family:"Roboto Slab",Georgia,serif;color:var(--text);background:var(--white)}
.section{position:relative;width:1200px;overflow:hidden}
.btn{display:inline-block;background:var(--btn-blue);color:var(--white);text-transform:uppercase;text-decoration:none;border-radius:2px;text-align:center}
.brand{display:flex;align-items:center;gap:10px;font-family:"Roboto",Arial,sans-serif;font-weight:700;font-size:21px;color:var(--blue);text-decoration:none}
.brand-dot{width:26px;height:26px;border-radius:50%;background:var(--yellow)}

/* header */
.site-header{height:72px;background:var(--white);box-shadow:0 1px 3px rgba(0,0,0,.12);z-index:2}
.site-header .brand{position:absolute;left:142px;top:22px}
.main-nav{position:absolute;left:451px;top:27px;display:flex;gap:0}
.main-nav a{font-size:16px;color:var(--text);text-decoration:none;margin-right:30px}
.main-nav a.active{color:var(--blue)}
.site-header .btn{position:absolute;left:886px;top:22px;width:142px;height:32px;line-height:32px;font-size:12px;font-weight:700;font-family:"Roboto",Arial,sans-serif}

/* hero */
.hero{height:598px}
.hero-photo{position:absolute;inset:0;background:linear-gradient(180deg,#d9d9d7 0%,#cfcfcd 55%,#b8b5b0 75%,#8f8a84 100%)}
.hero-title{position:absolute;top:262px;width:100%;text-align:center;font-size:59px;font-weight:700;color:#2b2b2b}
.hero .btn{position:absolute;left:497px;top:359px;width:206px;height:45px;line-height:45px;font-size:17px;font-weight:700;background:var(--blue)}
.hero-dots{position:absolute;top:570px;left:0;width:100%;display:flex;justify-content:center;gap:5px}
.hero-dots span{width:6px;height:6px;border-radius:50%;background:var(--white)}

/* services */
.services{height:538px;background:var(--mist)}
.section-title{text-align:center;font-size:41px;font-weight:400;color:#333}
.services .section-title{margin-top:32px}
.section-lead{width:580px;margin:18px auto 0;text-align:center;font-size:11px;line-height:20px;color:var(--text)}
.service-card{position:absolute;top:166px;width:272px;height:271px;background:var(--white);text-align:center}
.service-card:nth-of-type(1){left:171px}
.service-card:nth-of-type(2){left:464px}
.service-card:nth-of-type(3){left:755px}
.service-icon{width:68px;height:62px;margin:40px auto 0;border-radius:4px;background:linear-gradient(135deg,var(--ice),var(--lemon))}
.service-card h3{margin-top:24px;font-size:16px;font-weight:400;color:#333}
.service-card .rule{width:44px;height:2px;background:var(--yellow);margin:12px auto 14px}
.service-card p{font-size:11px;line-height:20px;color:var(--text);padding:0 28px}

/* about */
.about{height:592px;background:#f3f3f3}
.about-photo{position:absolute;left:0;top:0;width:600px;height:592px;background:linear-gradient(135deg,#e9e7e4 0%,#d8d6d2 50%,#a9a7a5 100%)}
.about-body{position:absolute;left:649px;top:66px;width:400px}
.about-body h2{font-size:30px;font-weight:400;color:#333;margin-left:1px}
.about-body .intro{margin-top:20px;font-size:11px;line-height:20px}
.check-list{list-style:none;margin-top:17px}
.check-list li{position:relative;padding-left:20px;font-size:11.5px;line-height:29.3px}
.check-list li::before{content:"";position:absolute;left:0;top:10px;width:10px;height:10px;border-radius:50%;background:var(--yellow);border:2px solid var(--sky)}
.about-body .btn{margin-top:30px;width:123px;height:37px;line-height:37px;font-size:12px}

/* testimonials */
.testimonials{height:446px;background:linear-gradient(160deg,#4ea9df 0%,#3597d4 50%,#2b8ccc 100%)}
.testimonials .section-title{color:var(--white);margin-top:122px}
.quote{position:absolute;top:209px;width:345px;text-align:center;color:var(--white)}
.quote p{font-size:12.5px;line-height:24px;font-style:italic}
.quote cite{display:block;margin-top:22px;font-style:normal;font-weight:700;font-size:14px}
.quote.side{opacity:.45}
.quote.left{left:30px}
.quote.center{left:428px}
.quote.right{left:825px}

/* blog */
.blog{height:597px}
.blog .section-title{margin-top:64px}
.post{position:absolute;top:143px;width:268px;height:365px;background:var(--white);box-shadow:0 1px 5px rgba(0,0,0,.18)}
.post:nth-of-type(1){left:171px}
.post:nth-of-type(2){left:465px}
.post:nth-of-type(3){left:758px}
.post-photo{height:164px;background:linear-gradient(135deg,var(--ice),var(--sky) 60%,#eee)}
.post-date{position:absolute;left:6px;top:6px;width:34px;height:42px;background:var(--yellow);text-align:center;font-weight:700;color:var(--ink);font-size:17px;line-height:20px;padding-top:3px}
.post-date small{display:block;font-size:10px;line-height:12px}
.post h3{margin:30px 24px 0;font-size:17px;font-weight:700;color:#222}
.post p{margin:12px 24px 0;font-size:11.5px;line-height:20px}
.post .btn{position:absolute;left:23px;top:305px;width:100px;height:31px;line-height:31px;font-size:11px}

/* contact */
.contact{height:572px;background:var(--yellow)}
.contact-photo{position:absolute;left:598px;top:0;width:602px;height:572px;background:linear-gradient(150deg,#7fc0e8 0%,#3d9fdc 45%,#1f6fb4 100%)}
.contact-body{position:absolute;left:172px;top:58px;width:390px}
.contact-body h2{font-size:30px;font-weight:400;color:#222;margin-left:5px}
.contact-body .intro{margin-top:10px;font-size:10.5px;line-height:20px;color:#333}
.estimate-form{margin-top:16px;width:350px}
.field{position:relative;height:39px;margin-bottom:7px;background:var(--white);border:1px solid #555;font-size:13px;line-height:37px;padding-left:10px;color:#222}
.field .caret{position:absolute;right:10px;top:0;font-size:8px}
.field svg{position:absolute;right:9px;top:13px}
.submit{margin-top:11px;height:37px;background:#000;color:var(--white);text-align:center;line-height:37px;font-weight:700;font-size:15px;font-family:"Roboto",Arial,sans-serif}

/* footer */
.site-footer{height:320px;background:var(--footer)}
.foot-col{position:absolute;top:62px}
.foot-col h4{font-size:15px;font-weight:700;color:#333;margin-bottom:10px}
.foot-col a{display:block;font-size:11.5px;line-height:23px;color:var(--muted);text-decoration:none}
.foot-col.c1{left:171px}.foot-col.c2{left:339px}.foot-col.c3{left:497px}
.newsletter{position:absolute;left:672px;top:62px}
.newsletter h4{font-size:15px;font-weight:700;color:#333}
.news-form{display:flex;margin-top:17px}
.news-input{width:268px;height:40px;background:var(--white);border:1px solid #ddd;font-size:11px;line-height:38px;padding-left:11px}
.news-btn{width:87px;height:40px;background:var(--btn-blue);color:var(--white);font-weight:700;font-size:14px;line-height:40px;text-align:center}
.social{display:flex;gap:12px;margin-top:13px;margin-left:2px}
.social span{width:24px;height:24px;border-radius:50%;background:#8a8a8a}
.foot-rule{position:absolute;left:171px;top:241px;width:850px;height:1px;background:var(--line)}
.site-footer .brand{position:absolute;left:142px;top:261px}
.copyright{position:absolute;right:179px;top:268px;font-size:11.5px;color:#333}
</style>
</head>
<body>

<header class="section site-header">
  <a class="brand" href="#"><span class="brand-dot"></span>Tidewell Homecare</a>
  <nav class="main-nav">
    <a class="active" href="#">Home</a>
    <a href="#">Services</a>
    <a href="#">About Us</a>
    <a href="#">News</a>
    <a href="#">Contact Us</a>
  </nav>
  <a class="btn" href="#">Free Estimate</a>
</header>

<section class="section hero">
  <div class="hero-photo" role="img" aria-label="Bright living room with a white sofa, armchair and coffee table"></div>
  <h1 class="hero-title">Tidewell Homecare</h1>
  <a class="btn" href="#">Free Estimate</a>
  <div class="hero-dots"><span></span><span></span><span></span><span></span></div>
</section>

<section class="section services">
  <h2 class="section-title">Our Services</h2>
  <p class="section-lead">Sed ut perspiciatis unde omnis iste natus error sit voluptatem accusantium doloremque laudantium, totam rem aperiam, eaque ipsa quae ab illo inventore veritatis et quasi architecto beatae vitae dicta sunt expli.</p>
  <article class="service-card">
    <div class="service-icon" role="img" aria-label="Bucket and broom icon"></div>
    <h3>Commercial Cleaning</h3><div class="rule"></div>
    <p>Seciatis unde omnis iste natussitta tem accusantium doloemue laudntiam remnis iste natussit voluptate</p>
  </article>
  <article class="service-card">
    <div class="service-icon" role="img" aria-label="Office desk and chair icon"></div>
    <h3>Office Cleaning</h3><div class="rule"></div>
    <p>Seciatis unde omnis iste natussitta tem accusantium doloemue laudntiam remnis iste natussit voluptate</p>
  </article>
  <article class="service-card">
    <div class="service-icon" role="img" aria-label="House with furniture icon"></div>
    <h3>Residential Cleaning</h3><div class="rule"></div>
    <p>Seciatis unde omnis iste natussitta tem accusantium doloemue laudntiam remnis iste natussit voluptate</p>
  </article>
</section>

<section class="section about">
  <div class="about-photo" role="img" aria-label="Housekeeper vacuuming a living room carpet"></div>
  <div class="about-body">
    <h2>About Tidewell Homecare</h2>
    <p class="intro">Sed ut perspiciatis unde omnis iste natus error sit voluptatem accusantium doloremque laudantium, totam rem aperiam, eaque ipsa quae ab illo.</p>
    <ul class="check-list">
      <li>Praesent eu libero ut eros egestas finibus.</li>
      <li>Donec eu ex sit amet tortor vestibulum accumsan.</li>
      <li>Sed dictum dolor quis lobortis viverra.</li>
      <li>Curabitur id lorem sed ante mollis placerat.</li>
      <li>Quisque malesuada dolor quis commodo suscipit.</li>
      <li>Fusce at sapien et dui facilisis rutrum nec quis magna.</li>
      <li>Nam posuere nibh id fringilla dapibus.</li>
      <li>Phasellus ut velit vitae diam varius interdum ut vel nisi.</li>
      <li>Phasellus et lacus sed libero congue tempor in se</li>
      <li>Phasellus ut velit vitae diam varius interdum ut vel nisi.</li>
    </ul>
    <a class="btn" href="#">Read More</a>
  </div>
</section>

<section class="section testimonials" role="img" aria-label="Blue background with a cleaner in soft focus">
  <h2 class="section-title">What Our Clients Says</h2>
  <blockquote class="quote side left"><p>“ Sed ut perspiciatis unde omnis iste natus error sit volu ptatem accusantium doloremque laudantium, totam rem aperiam, eaque ipsa quae ab illo inventore veritatis et qu asi architecto beatae vitae dicta sunt explica.”</p><cite>Jenna Cole Rutherford</cite></blockquote>
  <blockquote class="quote center"><p>“ Sed ut perspiciatis unde omnis iste natus error sit volu ptatem accusantium doloremque laudantium, totam rem aperiam, eaque ipsa quae ab illo inventore veritatis et qu asi architecto beatae vitae dicta sunt explica.”</p><cite>Jenna Cole Rutherford</cite></blockquote>
  <blockquote class="quote side right"><p>“ Sed ut perspiciatis unde omnis iste natus error sit volu ptatem accusantium doloremque laudantium, totam rem aperiam, eaque ipsa quae ab illo inventore veritatis et qu asi architecto beatae vitae dicta sunt explica.”</p><cite>Jenna Cole Rutherford</cite></blockquote>
</section>

<section class="section blog">
  <h2 class="section-title">Latest Blog</h2>
  <article class="post">
    <div class="post-photo" role="img" aria-label="Gloved hand spraying and wiping a bathroom sink"></div>
    <div class="post-date">12<small>APR</small></div>
    <h3>Sedperspiciatis mnis</h3>
    <p>Sed ut perspiciatis unde os istenatusr sit volptatem accutium doloremque la udantiued ut periciatis unde</p>
    <a class="btn" href="#">Read More</a>
  </article>
  <article class="post">
    <div class="post-photo" role="img" aria-label="Woman vacuuming a modern kitchen floor"></div>
    <div class="post-date">12<small>APR</small></div>
    <h3>Sedperspiciatis mnis</h3>
    <p>Sed ut perspiciatis unde os istenatusr sit volptatem accutium doloremque la udantiued ut periciatis unde</p>
    <a class="btn" href="#">Read More</a>
  </article>
  <article class="post">
    <div class="post-photo" role="img" aria-label="Woman dusting a wooden shelf"></div>
    <div class="post-date">12<small>APR</small></div>
    <h3>Sedperspiciatis mnis</h3>
    <p>Sed ut perspiciatis unde os istenatusr sit volptatem accutium doloremque la udantiued ut periciatis unde</p>
    <a class="btn" href="#">Read More</a>
  </article>
</section>

<section class="section contact">
  <div class="contact-body">
    <h2>Free Estimate/Contact Us</h2>
    <p class="intro">Sed ut perspiciatis unde omnis iste natus error sit voluptatem accusantium doloremque laudantium, totam rem aperiam, eaque ipsa quae ab illo.</p>
    <form class="estimate-form">
      <div class="field">Name:</div>
      <div class="field">Email:</div>
      <div class="field">Phone:</div>
      <div class="field">Type of Cleaning<span class="caret">▼</span></div>
      <div class="field">mm/dd/yyyy<svg width="12" height="12" viewBox="0 0 12 12"><rect x="1" y="2" width="10" height="9" fill="none" stroke="#333"/><line x1="1" y1="5" x2="11" y2="5" stroke="#333"/></svg></div>
      <div class="field">Property Type<span class="caret">▼</span></div>
      <div class="submit">SUBMIT</div>
    </form>
  </div>
  <div class="contact-photo" role="img" aria-label="Gloved hand carrying a blue bucket of cleaning supplies"></div>
</section>

<footer class="section site-footer">
  <div class="foot-col c1"><h4>Company</h4><a href="#">Home</a><a href="#">Services</a><a href="#">Blog</a><a href="#">Testimonials</a></div>
  <div class="foot-col c2"><h4>Links</h4><a href="#">Accusamus</a><a href="#">Dto odio dignis</a><a href="#">simos ducimus</a><a href="#">Lorequi bla</a></div>
  <div class="foot-col c3"><h4>Help</h4><a href="#">Accusamus</a><a href="#">Dto odio dignis</a><a href="#">simos ducimus</a><a href="#">Lorequi bla</a></div>
  <div class="newsletter">
    <h4>Sign up to our Newsletter</h4>
    <div class="news-form"><div class="news-input">Email:</div><div class="news-btn">Sign Up</div></div>
    <div class="social"><span></span><span></span><span></span><span></span></div>
  </div>
  <div class="foot-rule"></div>
  <a class="brand" href="#"><span class="brand-dot"></span>Tidewell Homecare</a>
  <p class="copyright">Copyright 2020 All Rights Reserved. Terms of Use | Privacy Policy</p>
</footer>

</body>
</html>
```